Brightfen Business Card Redesign & Logo Update

We need to update our business cards to something more modern and fresh. Brightfen can provide the current color schemes and old design examples, but welcome creativity in helping us with this redesign. PLEASE NOTE that we no longer utilize the "tree" and/or "leaf" imagery in our branding. If able would apprecaite an update on the quality of our "words only" logo in Ai. / PNG formats too.

Target Market(s)

Investors, landowners, corporate partners, contractors

Industry/Entity Type

Environmental Restoration & Conservation

Contact Information for Business Card

Logo, persons name, title, mailing address, phone and email, website url

Font styles to use
Other font styles liked:
• Merriweather

Requirements
Nice to have
• Logo, persons name, title, mailing address, phone and email, website url, but open to ideams
Should not have
• No all back backgrounds

```html
<!DOCTYPE html>
<html lang="en">
<head>
<meta charset="utf-8">
<title>Brightfen Business Card</title>
<link rel="stylesheet" href="https://fonts.googleapis.com/css2?family=Oswald:wght@500;700&family=Roboto:wght@400&display=swap">
<style>
  :root {
    --backdrop: #2a2624;
    --card-dark: #1b1b1b;
    --card-light: #ffffff;
    --orange: #ee7d00;
    --green: #17793a;
    --leaf-green: #5fb02f;
    --text-light: #e8e8e8;
  }
  * { margin: 0; padding: 0; box-sizing: border-box; }
  html, body { width: 1200px; height: 842px; overflow: hidden; }
  body {
    background: var(--backdrop);
    position: relative;
    font-family: "Roboto", sans-serif;
  }
  .card {
    position: absolute;
    top: 266px;
    width: 540px;
    height: 310px;
    overflow: hidden;
    box-shadow: 0 10px 28px rgba(0,0,0,0.45);
  }
  /* Back of card: contact details */
  .card-back { left: 40px; background: var(--card-dark); }
  .band { position: absolute; left: 0; width: 100%; height: 14px; background: var(--orange); }
  .band-top { top: 0; }
  .band-bottom { top: 272px; }
  .contact-block {
    position: absolute;
    left: 150px;
    top: 64px;
    color: var(--text-light);
  }
  .person-name {
    font-family: "Oswald", sans-serif;
    font-weight: 500;
    font-size: 32px;
    line-height: 1;
    color: var(--leaf-green);
    letter-spacing: -0.5px;
  }
  .person-title {
    font-size: 15px;
    letter-spacing: 1.5px;
    color: var(--orange);
    margin-top: 3px;
  }
  .divider {
    width: 64px;
    height: 1px;
    background: var(--leaf-green);
    margin: 12px 0 10px 40px;
  }
  .contact-line {
    font-size: 15px;
    line-height: 20px;
    letter-spacing: 0.6px;
  }
  .address { margin-top: 16px; }

  /* Front of card: wordmark */
  .card-front { left: 620px; background: var(--card-light); }
  .edge-block { position: absolute; background: var(--orange); }
  .edge-rule { position: absolute; width: 5px; background: var(--green); }
  .edge-block-left { left: 0; top: 168px; width: 54px; height: 76px; }
  .edge-rule-left { left: 64px; top: 168px; height: 76px; }
  .edge-block-right { right: 0; top: 56px; width: 54px; height: 64px; }
  .edge-rule-right { right: 64px; top: 56px; height: 64px; }
  .wordmark {
    position: absolute;
    left: 0;
    width: 100%;
    top: 108px;
    text-align: center;
    font-family: "Oswald", sans-serif;
    font-weight: 700;
    font-size: 70px;
    line-height: 1;
    color: var(--green);
    letter-spacing: 1px;
  }
</style>
</head>
<body>
  <section class="card card-back">
    <div class="band band-top"></div>
    <div class="contact-block">
      <p class="person-name">MARCUS HALE</p>
      <p class="person-title">MANAGING DIRECTOR</p>
      <div class="divider"></div>
      <p class="contact-line">044-987 654 321</p>
      <p class="contact-line">INFO@BRIGHTFENMAIL.COM</p>
      <p class="contact-line">WWW.BRIGHTFENSITE.COM</p>
      <div class="divider"></div>
      <p class="contact-line address">88, MARSH LANE ROAD</p>
      <p class="contact-line">20917, FENLAND</p>
    </div>
    <div class="band band-bottom"></div>
  </section>

  <section class="card card-front">
    <div class="edge-block edge-block-left"></div>
    <div class="edge-rule edge-rule-left"></div>
    <p class="wordmark">BRIGHTFEN</p>
    <div class="edge-rule edge-rule-right"></div>
    <div class="edge-block edge-block-right"></div>
  </section>
</body>
</html>
```